BRAVO Estate Attendant

We require a website built for this company. Logo is also on the attached document. Some info on the company:<br/>To create a work class experience for our clients for property maintenance. A personalised service that deliver’s what landlords need...Quality work, on time and managed from start to finish.<br/>We do things different, our clients deal with one contact, a client manager who manages your maintenance task from start to finish. Our service allows our expert trades people to do what they do best and leave the management/organising to us!<br/>I have drafted up the layout of the web ... very brief at this stage however once we have more info we will add links and can collate more information and provide. <br/>We just want to get a layout of what you think the web should look like and can go from there.

```html
<!DOCTYPE html>
<html lang="en">
<head>
<meta charset="utf-8">
<title>BRAVO Estate Attendant</title>
<link rel="stylesheet" href="https://fonts.googleapis.com/css2?family=Poppins:wght@400;500;600;700&display=swap">
<style>
:root{
  --yellow:#ffc600;
  --yellow-pale:#ffe8a0;
  --dark:#333333;
  --topbar:#3a3a3a;
  --footer:#3d3d3d;
  --text:#4a4a4a;
  --muted:#b5b5b5;
  --light-bg:#f5f5f5;
  --white:#ffffff;
}
*{box-sizing:border-box;margin:0;padding:0}
html,body{width:1200px;height:2344px;overflow:hidden;background:var(--white)}
body{font-family:'Poppins',sans-serif;color:var(--text)}
.canvas{position:relative;width:1200px;height:2344px;overflow:hidden}
.abs{position:absolute}

/* top bar */
.topbar{top:0;left:0;width:1200px;height:32px;background:var(--topbar)}
.topbar-phone{left:0;top:0;width:397px;height:32px;background:var(--yellow)}
.topbar-text{font-size:9.5px;color:var(--white);top:10px;white-space:nowrap}
.topbar-text b{font-weight:600}
.social-dot{width:8px;height:8px;border-radius:50%;background:var(--white);top:12px}

/* header */
.header{top:32px;left:0;width:1200px;height:72px;background:var(--white)}
.brand{left:234px;top:56px;font-size:18px;font-weight:600;color:var(--dark);letter-spacing:.2px;white-space:nowrap}
.nav a{position:absolute;top:66px;font-size:10.5px;font-weight:600;color:var(--dark);text-decoration:none;text-transform:uppercase;white-space:nowrap}
.nav a.active{color:var(--yellow)}
.nav-sep{left:917px;top:62px;width:1px;height:18px;background:#ddd}
.search-btn{left:933px;top:62px;width:19px;height:19px;border-radius:50%;background:#eee}

/* hero */
.hero{top:104px;left:0;width:1200px;height:467px}
.hero-title{top:282px;left:0;width:1200px;text-align:center;font-size:21px;font-weight:700;color:var(--yellow)}
.hero-sub{top:316px;left:0;width:1200px;text-align:center;font-size:15.5px;color:var(--white);line-height:23px}
.hero-arrow{top:279px;width:34px;height:34px;background:var(--white)}
.hero-dots span{position:absolute;top:511px;width:22px;height:2px;background:var(--white)}

/* welcome */
.eyebrow-dots{width:11px;height:6px}
.welcome-eyebrow{left:260px;top:640px;font-size:11px;font-weight:600;color:#777;letter-spacing:.3px}
.welcome-title{left:260px;top:658px;font-size:15px;font-weight:600;color:var(--dark)}
.hl{color:var(--yellow)}
.welcome-lead{left:234px;top:693px;width:336px;font-size:10.4px;font-weight:500;color:var(--dark);line-height:17.5px}
.welcome-body{left:234px;top:763px;width:336px;font-size:10.4px;line-height:17.5px;color:#555}
.btn-outline{left:234px;top:909px;width:84px;height:28px;border:1.5px solid var(--yellow);border-radius:14px;color:var(--yellow);font-size:9.5px;font-weight:600;text-align:center;line-height:25px}

/* services */
.services{top:1005px;left:0;width:1200px;height:537px}
.section-title{left:0;width:1200px;text-align:center;font-size:19px;font-weight:700;color:var(--dark)}
.service-card{width:231px;height:171px;background:var(--white);border:1px solid #efefef}
.service-card svg{position:absolute;left:21px;top:20px}
.service-name{position:absolute;left:75px;top:32px;width:145px;font-size:11.5px;font-weight:600;color:var(--dark);line-height:14px}
.service-name.two{top:25px}
.service-text{position:absolute;left:20px;top:69px;width:200px;font-size:8.6px;line-height:16.3px;color:#555}

/* team */
.team-card{top:1667px;width:231px;height:263px}
.team-photo{position:absolute;left:0;top:0;width:231px;height:209px}
.team-social{position:absolute;left:0;top:155px;width:231px;height:54px;background:rgba(235,235,235,.85)}
.team-social span{position:absolute;top:22px;width:12px;height:12px;border-radius:50%;background:var(--dark)}
.team-name{position:absolute;left:0;top:209px;width:231px;height:54px;background:var(--yellow);color:var(--white);font-size:12.5px;font-weight:700;text-align:center;line-height:54px;text-transform:uppercase}

/* footer */
.footer{top:1984px;left:0;width:1200px;height:360px}
.footer-brand{left:233px;top:2098px;font-size:14px;font-weight:600;color:var(--white);white-space:nowrap}
.footer-about{left:233px;top:2146px;width:170px;font-size:9px;line-height:16.2px;color:#d8d8d8}
.footer-head{top:2083px;font-size:9.5px;font-weight:600;color:var(--white);text-transform:uppercase;white-space:nowrap}
.footer-list{list-style:none;top:2108px}
.footer-list li{font-size:9px;color:#d8d8d8;height:18.7px;white-space:nowrap}
.contact-row{left:797px;font-size:9px;color:#d8d8d8;line-height:15px}
.contact-row svg{position:absolute;left:2px;top:2px}
.contact-row span{position:absolute;left:20px;top:0;white-space:nowrap}
.footer-rule{left:233px;top:2258px;width:732px;height:1px;background:#555}
.footer-small{top:2281px;font-size:9px;color:#9a9a9a;white-space:nowrap}
.mail-btn{left:1105px;top:2248px;width:40px;height:40px;border-radius:50%;background:var(--yellow)}
</style>
</head>
<body>
<div class="canvas">

  <!-- top bar -->
  <div class="abs topbar"></div>
  <div class="abs topbar-phone"></div>
  <svg class="abs" style="left:234px;top:10px" width="7" height="11" viewBox="0 0 7 11"><rect x=".6" y=".6" width="5.8" height="9.8" rx="1" fill="none" stroke="#fff" stroke-width="1.2"/></svg>
  <div class="abs topbar-text" style="left:247px"><b>Client Services:</b> 02 5550 0142</div>
  <svg class="abs" style="left:675px;top:12px" width="9" height="7" viewBox="0 0 9 7"><rect x=".5" y=".5" width="8" height="6" fill="none" stroke="#fff"/><path d="M.5 .5L4.5 4L8.5 .5" fill="none" stroke="#fff"/></svg>
  <div class="abs topbar-text" style="left:689px"><b>Email:</b> info@bravoestateattendant.com</div>
  <div class="abs" style="left:879px;top:9px;width:1px;height:14px;background:#666"></div>
  <div class="abs social-dot" style="left:893px"></div>
  <div class="abs social-dot" style="left:907px"></div>
  <div class="abs social-dot" style="left:923px"></div>
  <div class="abs social-dot" style="left:941px"></div>

  <!-- header -->
  <div class="abs header"></div>
  <div class="abs brand">BRAVO Estate Attendant</div>
  <nav class="nav">
    <a class="active" style="left:546px">Home</a>
    <a style="left:603px">About Us</a>
    <a style="left:680px">Services ⌄</a>
    <a style="left:763px">Benefit ⌄</a>
    <a style="left:839px">Contact Us</a>
  </nav>
  <div class="abs nav-sep"></div>
  <div class="abs search-btn"></div>
  <svg class="abs" style="left:939px;top:68px" width="8" height="8" viewBox="0 0 8 8"><circle cx="3.3" cy="3.3" r="2.5" fill="none" stroke="#555" stroke-width="1"/><path d="M5.2 5.2L7.5 7.5" stroke="#555"/></svg>

  <!-- hero -->
  <svg class="abs hero" viewBox="0 0 1200 467">
    <defs>
      <linearGradient id="heroTone" x1="0" y1="0" x2="1" y2="1">
        <stop offset="0" stop-color="#b8392c"/>
        <stop offset=".35" stop-color="#c89078"/>
        <stop offset=".7" stop-color="#9b8d85"/>
        <stop offset="1" stop-color="#6e6b6a"/>
      </linearGradient>
    </defs>
    <path role="img" aria-label="Photo of hands passing a stack of coins" d="M0 0H1200V350Q600 556 0 350Z" fill="url(#heroTone)"/>
    <path d="M0 0H1200V350Q600 556 0 350Z" fill="#000" opacity=".22"/>
    <path d="M0 350Q600 556 1200 350Q600 584 0 350Z" fill="var(--yellow)"/>
  </svg>
  <div class="abs hero-title">HOW CAN WE HELP YOU?</div>
  <div class="abs hero-sub">Wealth management and financial advisory company with a<br>strong commitment to the local community</div>
  <div class="abs hero-arrow" style="left:93px"><svg width="34" height="34" viewBox="0 0 34 34"><path d="M19 12L14 17L19 22" fill="none" stroke="#333" stroke-width="1.5"/></svg></div>
  <div class="abs hero-arrow" style="left:1073px"><svg width="34" height="34" viewBox="0 0 34 34"><path d="M15 12L20 17L15 22" fill="none" stroke="#333" stroke-width="1.5"/></svg></div>
  <div class="hero-dots">
    <span style="left:564px;background:var(--yellow)"></span>
    <span style="left:590px"></span>
    <span style="left:616px"></span>
  </div>

  <!-- welcome -->
  <svg class="abs eyebrow-dots" style="left:235px;top:642px" viewBox="0 0 11 6"><g fill="var(--yellow)"><circle cx="1" cy="1" r="1"/><circle cx="4" cy="1" r="1"/><circle cx="7" cy="1" r="1"/><circle cx="10" cy="1" r="1"/><circle cx="1" cy="4" r="1"/><circle cx="4" cy="4" r="1"/><circle cx="7" cy="4" r="1"/></g></svg>
  <div class="abs welcome-eyebrow">WELCOME TO</div>
  <div class="abs welcome-title">BRAVO <span class="hl">ESTATE</span> ATTENDANT</div>
  <p class="abs welcome-lead">Lorem ipsum dolor sit amet, consectetur adipiscing elit. Cras vitae orci lacinia dolor porta elementum vitae non nisl. Duis porttitor rutrum rhoncus.</p>
  <p class="abs welcome-body">Cras neque tellus, hendrerit nec tristique ut, dictum ac massa. Vivamus semper leo vel pellentesque suscipit. Mauris eget purus ligula. Sed nisl risus, mattis id risus tempus, sagittis tempor eros. In hac habitasse platea dictumst. Curabitur ac risus non ante fringilla tincidunt sit amet vitae ligula. Donec lacus tellus, gravida eu augue a, sollicitudin scelerisque turpis. Quisque at leo non metus posuere ultrices id non sem.</p>
  <div class="abs btn-outline">READ MORE</div>

  <svg class="abs" style="left:612px;top:614px" width="338" height="338" viewBox="0 0 338 338">
    <defs>
      <linearGradient id="planTone" x1="0" y1="0" x2="1" y2="1">
        <stop offset="0" stop-color="#8a8f96"/>
        <stop offset=".45" stop-color="#e6e3dc"/>
        <stop offset="1" stop-color="#7d6f60"/>
      </linearGradient>
    </defs>
    <circle cx="169" cy="169" r="168" fill="var(--yellow-pale)"/>
    <circle role="img" aria-label="Video still of a team reviewing floor plans on a desk" cx="169" cy="169" r="156" fill="url(#planTone)"/>
    <circle cx="169" cy="169" r="23" fill="var(--yellow)"/>
    <path d="M163 159L179 169L163 179Z" fill="none" stroke="#fff" stroke-width="2" stroke-linejoin="round"/>
  </svg>

  <!-- services -->
  <div class="abs services" role="img" aria-label="Faint architectural floor plan backdrop" style="background:var(--light-bg)"></div>
  <svg class="abs eyebrow-dots" style="left:594px;top:1054px" viewBox="0 0 11 6"><g fill="var(--yellow)"><circle cx="1" cy="1" r="1"/><circle cx="4" cy="1" r="1"/><circle cx="7" cy="1" r="1"/><circle cx="10" cy="1" r="1"/><circle cx="1" cy="4" r="1"/><circle cx="4" cy="4" r="1"/><circle cx="7" cy="4" r="1"/></g></svg>
  <div class="abs section-title" style="top:1066px">OUR <span class="hl">SERVICES</span></div>

  <div class="abs service-card" style="left:234px;top:1126px">
    <svg width="40" height="40" viewBox="0 0 40 40" fill="none" stroke="#333" stroke-width="1.4"><circle cx="20" cy="12" r="5"/><path d="M10 30V24Q10 19 20 19Q30 19 30 24V30"/><path d="M4 34H36"/><rect x="15" y="2" width="10" height="3" fill="var(--yellow)" stroke="none"/></svg>
    <div class="service-name">Trade People</div>
    <p class="service-text">Lorem ipsum dolor sit amet, consectetur adipiscing elit. Cras vitae orci lacinia dolor porta elementum vitae non nisl. Duis porttitor rutrum rhoncus. Orci varius natoque penatibus et magnis dis parturient montes</p>
  </div>
  <div class="abs service-card" style="left:484px;top:1126px">
    <svg width="42" height="40" viewBox="0 0 42 40" fill="none" stroke="#333" stroke-width="1.4"><rect x="2" y="13" width="26" height="14" fill="var(--yellow)"/><path d="M28 17H35L40 22V27H28Z"/><circle cx="9" cy="29" r="3" fill="#fff"/><circle cx="33" cy="29" r="3" fill="#fff"/></svg>
    <div class="service-name two">Removalist Van and Trailers</div>
    <p class="service-text">Lorem ipsum dolor sit amet, consectetur adipiscing elit. Cras vitae orci lacinia dolor porta elementum vitae non nisl. Duis porttitor rutrum rhoncus. Orci varius natoque penatibus et magnis dis parturient montes</p>
  </div>
  <div class="abs service-card" style="left:734px;top:1126px">
    <svg width="42" height="40" viewBox="0 0 42 40" fill="none" stroke="#333" stroke-width="1.4"><circle cx="21" cy="20" r="7" fill="var(--yellow)"/><circle cx="21" cy="5" r="3"/><circle cx="21" cy="35" r="3"/><circle cx="6" cy="20" r="3"/><circle cx="36" cy="20" r="3"/><path d="M21 8V13M21 27V32M9 20H14M28 20H33"/></svg>
    <div class="service-name">Connections</div>
    <p class="service-text">Lorem ipsum dolor sit amet, consectetur adipiscing elit. Cras vitae orci lacinia dolor porta elementum vitae non nisl. Duis porttitor rutrum rhoncus. Orci varius natoque penatibus et magnis dis parturient montes</p>
  </div>
  <div class="abs service-card" style="left:234px;top:1317px">
    <svg width="42" height="42" viewBox="0 0 42 42" fill="none" stroke="#333" stroke-width="1.4"><rect x="3" y="4" width="36" height="14"/><rect x="7" y="10" width="28" height="4" fill="var(--yellow)"/><path d="M12 24Q9 29 12 34M21 24Q18 29 21 34M30 24Q27 29 30 34" stroke-width="2"/></svg>
    <div class="service-name">Smoke Alarms</div>
    <p class="service-text">Lorem ipsum dolor sit amet, consectetur adipiscing elit. Cras vitae orci lacinia dolor porta elementum vitae non nisl. Duis porttitor rutrum rhoncus. Orci varius natoque penatibus et magnis dis parturient montes</p>
  </div>
  <div class="abs service-card" style="left:484px;top:1317px">
    <svg width="42" height="42" viewBox="0 0 42 42" fill="none" stroke="#333" stroke-width="1.4"><rect x="2" y="10" width="38" height="26" rx="2" fill="var(--yellow)"/><path d="M15 10V5H27V10M2 20H40"/><rect x="18" y="18" width="6" height="5" fill="#fff"/></svg>
    <div class="service-name">Finance</div>
    <p class="service-text">Lorem ipsum dolor sit amet, consectetur adipiscing elit. Cras vitae orci lacinia dolor porta elementum vitae non nisl. Duis porttitor rutrum rhoncus. Orci varius natoque penatibus et magnis dis parturient montes</p>
  </div>
  <div class="abs service-card" style="left:734px;top:1317px">
    <svg width="42" height="42" viewBox="0 0 42 42" fill="none" stroke="#333" stroke-width="1.4"><path d="M9 12H33L39 19L21 38L3 19Z" fill="var(--yellow)"/><path d="M3 19H39M15 12L21 38L27 12"/><path d="M21 2V7M10 5L12 8M32 5L30 8"/></svg>
    <div class="service-name">Wealth Creation</div>
    <p class="service-text">Lorem ipsum dolor sit amet, consectetur adipiscing elit. Cras vitae orci lacinia dolor porta elementum vitae non nisl. Duis porttitor rutrum rhoncus. Orci varius natoque penatibus et magnis dis parturient montes</p>
  </div>

  <!-- team -->
  <svg class="abs eyebrow-dots" style="left:594px;top:1597px" viewBox="0 0 11 6"><g fill="var(--yellow)"><circle cx="1" cy="1" r="1"/><circle cx="4" cy="1" r="1"/><circle cx="7" cy="1" r="1"/><circle cx="10" cy="1" r="1"/><circle cx="1" cy="4" r="1"/><circle cx="4" cy="4" r="1"/><circle cx="7" cy="4" r="1"/></g></svg>
  <div class="abs section-title" style="top:1609px">OUR <span class="hl">TEAM</span></div>

  <div class="abs team-card" style="left:234px">
    <div class="team-photo" role="img" aria-label="Portrait of a team member in a yellow hard hat" style="background:linear-gradient(180deg,#6c6c6c,#9a9a9a)"></div>
    <div class="team-social"><span style="left:64px"></span><span style="left:88px"></span><span style="left:112px"></span><span style="left:138px;border-radius:3px;width:16px"></span></div>
    <div class="team-name">Callum Dreyer</div>
  </div>
  <div class="abs team-card" style="left:484px">
    <div class="team-photo" role="img" aria-label="Portrait of a team member in a blue hard hat on a building site" style="background:linear-gradient(180deg,#b59a7a,#2f3a4d)"></div>
    <div class="team-name">Maya Lindqvist</div>
  </div>
  <div class="abs team-card" style="left:734px">
    <div class="team-photo" role="img" aria-label="Portrait of a team member in a white hard hat giving a thumbs up" style="background:linear-gradient(180deg,#ececec,#4a86c8)"></div>
    <div class="team-name">Theo Barnes</div>
  </div>

  <!-- footer -->
  <svg class="abs footer" viewBox="0 0 1200 360">
    <path d="M0 118Q600 -100 1200 118V360H0Z" fill="var(--footer)"/>
    <path d="M0 118Q600 -118 1200 118Q600 -100 0 118Z" fill="var(--yellow)"/>
  </svg>
  <div class="abs footer-brand">BRAVO Estate Attendant</div>
  <p class="abs footer-about">Lorem ipsum dolor sit amet, consectetur adipiscing elit. Cras vitae orci lacinia dolor porta elementum vitae non nisl. Duis porttitor rutrum rhoncus.</p>

  <div class="abs footer-head" style="left:430px">Quick Links</div>
  <ul class="abs footer-list" style="left:430px"><li>Home</li><li>About Us</li><li>Services</li><li>Benefit</li><li>Contact Us</li></ul>

  <div class="abs footer-head" style="left:534px">Services</div>
  <ul class="abs footer-list" style="left:534px"><li>Trade People</li><li>Removalist Van and Trailers</li><li>Connections</li><li>Smoke Alarms</li><li>Finance</li><li>Wealth Creation</li></ul>

  <div class="abs footer-head" style="left:687px">Benefit</div>
  <ul class="abs footer-list" style="left:687px"><li>Customer Service</li><li>Call Centre</li><li>Values</li><li>Pricing</li><li>Level of Expertise</li></ul>

  <div class="abs footer-head" style="left:797px;top:2080px">Contact Info</div>
  <div class="abs contact-row" style="top:2110px"><svg width="10" height="10" viewBox="0 0 10 10"><path d="M1 1.5L3 1L4.3 3.5L3.2 4.5Q4.5 6.5 5.7 6.9L6.7 5.8L9 7.1L8.6 9Q3 9 1 1.5Z" fill="#fff"/></svg><span>02 5550 0142</span></div>
  <div class="abs contact-row" style="top:2132px"><svg width="10" height="9" viewBox="0 0 10 9"><rect x="0" y="1" width="10" height="7" fill="#fff"/><path d="M0 1L5 5L10 1" fill="none" stroke="#3d3d3d"/></svg><span>info@bravoestateattendant.com</span></div>
  <div class="abs contact-row" style="top:2156px;height:30px"><svg width="8" height="11" viewBox="0 0 8 11"><path d="M4 11Q0 5.5 0 4A4 4 0 0 1 8 4Q8 5.5 4 11Z" fill="#fff"/><circle cx="4" cy="4" r="1.4" fill="#3d3d3d"/></svg><span>4/18 Walker Street,<br>Seaview NSW</span></div>

  <div class="abs footer-rule"></div>
  <div class="abs footer-small" style="left:233px">Copyright © 2019 BRAVO Estate Attendant All rights reserved.</div>
  <div class="abs footer-small" style="left:810px">Terms &amp; Conditions &nbsp;|&nbsp; Privacy Policy</div>
  <div class="abs mail-btn"><svg width="40" height="40" viewBox="0 0 40 40"><rect x="12" y="14" width="16" height="12" rx="1.5" fill="none" stroke="#fff" stroke-width="1.6"/><path d="M12.5 15L20 21L27.5 15" fill="none" stroke="#fff" stroke-width="1.6"/></svg></div>

</div>
</body>
</html>
```